Business Card Design Project

We are looking to redesign the logo, business card and stationary of one of our group companies - SOLARO SUPPLY HOUSE LLC.

The company specialises in industrial PVC and CPVC Piping systems. It is situated in the Middle East and the focus is purely in this region.

The logo work is already completed. The file is uploaded for the reference.

We are looking for a clean minimalistic design for the business card.

regards
Rohit
Updates

Hello Everyone!

Thanks for submitting your designs. 

Yet to find the right design. Probably the below links will give you guys some more idea on what we would like.

Minimalist design with some creativity.

Rohit

http://exampledesignfolio.com/inspiration/15-beautifully-minimal-business-cards

http://www.samplelayoutbase.com/2011/11/14/30-minimalist-business-card-design/

http://www.primepixelcraft.com/inspiration/minimal-business-cards/

Target Market(s)

Industrial users

Industry/Entity Type

Industrial

Requirements
Must have
• - Minimalistic design

- Back side of the card should include the manufacturer PIPEMARQ NORTHERN's decal. The file is upload for the reference

- Further information
Company Name:
SOLARO SUPPLY HOUSE LLC
Address:
PO Box 8152, Sharjah Industrial Area 4, Qarwan Road
Sharjah, United Arab Emirates
Telephone:
+971-6-5000-118
Fax:
+977-6-5000-119
Email:
mail@sshlexample.com

- FYI, Solaro Supply House LLC is the authorised distributor for PIPEMARQ NORTHERN in the UAE. For further information on pipemarq please visit the website www.pipemarq-example.ca

```html
<!DOCTYPE html>
<html lang="en">
<head>
<meta charset="utf-8">
<title>Solaro Supply House LLC – Business Card</title>
<link rel="stylesheet" href="https://fonts.googleapis.com/css2?family=Arimo:wght@700&display=swap">
<style>
  :root {
    --paper: #ffffff;
    --fitting-light: #f1f1f1;
    --fitting-mid: #dcdcdc;
    --title-blue: #2f7fcb;
    --phone-blue: #1f5aa8;
    --mail-blue: #2f7fcb;
    --address-grey: #6b6b6b;
    --mark-dark: #1c1c1c;
  }
  * { margin: 0; padding: 0; box-sizing: border-box; }
  html, body { width: 1200px; height: 686px; overflow: hidden; background: var(--paper); }
  .card {
    position: relative;
    width: 1200px;
    height: 686px;
    background: var(--paper);
    font-family: "Arimo", Arial, sans-serif;
    font-weight: 700;
    overflow: hidden;
  }
  .card__backdrop {
    position: absolute;
    inset: 0;
    background:
      radial-gradient(circle at 250px 590px, var(--fitting-mid) 0 120px, transparent 210px),
      radial-gradient(circle at 960px 520px, var(--fitting-mid) 0 150px, transparent 290px),
      radial-gradient(ellipse at 470px 260px, var(--fitting-light) 0 260px, transparent 420px),
      linear-gradient(180deg, #f6f6f6 0%, var(--paper) 60%, #f4f4f4 100%);
    opacity: 0.85;
  }
  .company-name {
    position: absolute;
    top: 94px;
    left: 0;
    width: 1200px;
    text-align: center;
    font-size: 51px;
    letter-spacing: 0.5px;
    color: var(--title-blue);
    text-shadow: 2px 4px 6px rgba(0,0,0,0.25);
  }
  .contact {
    position: absolute;
    right: 40px;
    top: 280px;
    text-align: right;
  }
  .contact__address {
    font-style: normal;
    font-size: 25px;
    line-height: 34.3px;
    color: var(--address-grey);
  }
  .contact__phones {
    margin-top: 6px;
    font-size: 30px;
    line-height: 40px;
    color: var(--phone-blue);
  }
  .brand {
    position: absolute;
    top: 548px;
    left: 0;
    width: 1200px;
    display: flex;
    justify-content: center;
    align-items: center;
    gap: 10px;
    font-size: 22px;
    color: var(--mark-dark);
  }
  .brand__square {
    width: 22px;
    height: 22px;
    background: var(--mark-dark);
    border-radius: 4px;
  }
  .email {
    position: absolute;
    top: 628px;
    left: 0;
    width: 1200px;
    text-align: center;
    font-size: 25px;
    color: var(--mail-blue);
  }
</style>
</head>
<body>
  <main class="card">
    <div class="card__backdrop" role="img" aria-label="Faded photograph of PVC pipe fittings"></div>
    <h1 class="company-name">SOLARO SUPPLY HOUSE LLC</h1>
    <section class="contact">
      <address class="contact__address">
        PO Box 8152<br>
        Sharjah Industrial Area 4<br>
        Qarwan Road<br>
        Sharjah<br>
        United Arab Emirates
      </address>
      <div class="contact__phones">
        <div class="contact__phone">+971-6-5000-118</div>
        <div class="contact__fax">+977-6-5000-119</div>
      </div>
    </section>
    <div class="brand">
      <span class="brand__square"></span>
      <span class="brand__name">SOLARO</span>
    </div>
    <div class="email">mail@sshlexample.com</div>
  </main>
</body>
</html>
```